Frostvale Harborline LLC

we need a business card design

Industry/Entity Type

hvac

Contact Information for Business Card

my logo

Requirements
Must have
• my logo and same colors

```html
<!DOCTYPE html>
<html lang="en">
<head>
<meta charset="utf-8">
<title>Frostvale Harborline LLC — Business Card</title>
<link href="https://fonts.googleapis.com/css2?family=Montserrat:wght@400;500;700&display=swap" rel="stylesheet">
<style>
  :root {
    --canvas: #ece7df;
    --card-front: #f4b960;
    --card-back: #ffffff;
    --brand-blue: #2a6db3;
    --ink: #3a3a3a;
    --accent: #f0a93a;
    --shadow: rgba(0,0,0,0.18);
  }
  html, body {
    margin: 0;
    width: 1200px;
    height: 913px;
    overflow: hidden;
    background: var(--canvas);
    font-family: "Montserrat", Arial, sans-serif;
  }
  .canvas { position: relative; width: 1200px; height: 913px; }
  .card {
    position: absolute;
    width: 540px;
    height: 309px;
    border-radius: 4px;
    box-shadow: 0 10px 24px var(--shadow);
    overflow: hidden;
  }
  .card--front {
    left: 70px; top: 130px;
    background: var(--card-front);
    display: flex; align-items: center; justify-content: center;
  }
  .brand-name {
    color: var(--brand-blue);
    font-weight: 700;
    text-align: center;
    margin: 0;
  }
  .card--front .brand-name { font-size: 34px; line-height: 1.15; }
  .card--back {
    left: 590px; top: 470px;
    background: var(--card-back);
  }
  .card--back .brand-name {
    position: absolute; right: 34px; top: 30px;
    font-size: 18px; line-height: 1.2; text-align: right;
  }
  .person { position: absolute; left: 40px; top: 128px; }
  .person__name { margin: 0; color: var(--brand-blue); font-weight: 700; font-size: 20px; }
  .person__title { margin: 3px 0 0; color: var(--ink); font-size: 12px; font-weight: 500; }
  .contacts { position: absolute; left: 40px; bottom: 30px; list-style: none; margin: 0; padding: 0; }
  .contacts li { display: flex; align-items: center; gap: 10px; color: var(--ink); font-size: 12.5px; margin-top: 6px; }
  .contacts svg { width: 13px; height: 13px; flex: none; }
  .address { position: absolute; right: 34px; top: 120px; margin: 0; color: var(--ink); font-size: 12px; line-height: 1.45; text-align: right; font-style: normal; }
</style>
</head>
<body>
<main class="canvas">
  <section class="card card--front" aria-label="Card front">
    <p class="brand-name">Frostvale<br>Harborline LLC</p>
  </section>

  <section class="card card--back" aria-label="Card back">
    <p class="brand-name">Frostvale<br>Harborline LLC</p>

    <div class="person">
      <h1 class="person__name">Dana Whitlock</h1>
      <p class="person__title">Managing Director</p>
    </div>

    <address class="address">48 Larkspur Avenue,<br>Eastbrook, NY 10000</address>

    <ul class="contacts">
      <li>
        <svg viewBox="0 0 14 14" aria-hidden="true"><rect x="3" y="1" width="8" height="12" rx="1.5" fill="none" stroke="var(--accent)" stroke-width="1.4"/><circle cx="7" cy="11" r="0.8" fill="var(--accent)"/></svg>
        +1 (555) 010-2468
      </li>
      <li>
        <svg viewBox="0 0 14 14" aria-hidden="true"><rect x="1" y="3" width="12" height="8" rx="1" fill="var(--accent)"/><path d="M1.5 3.5 L7 8 L12.5 3.5" fill="none" stroke="#fff" stroke-width="1"/></svg>
        info@frostvaleharbor.com
      </li>
      <li>
        <svg viewBox="0 0 14 14" aria-hidden="true"><circle cx="7" cy="7" r="5.5" fill="none" stroke="var(--accent)" stroke-width="1.4"/><path d="M1.5 7 H12.5 M7 1.5 C4.5 4.5 4.5 9.5 7 12.5 M7 1.5 C9.5 4.5 9.5 9.5 7 12.5" fill="none" stroke="var(--accent)" stroke-width="1"/></svg>
        www.frostvaleharbor.com
      </li>
    </ul>
  </section>
</main>
</body>
</html>
```